Civil Engineering Business Card Design

We need a business card design for an Civil Engineering Company located in Naples, Florida. The company name is Durvel Engineering.
What we do:
Site Evaluation
Review existing site conditions and zoning
Evaluation of potential development options
Evaluation of environmental permitting challenges
Prepare alternative master site development or redevelopment plan
Calculate cost and time lines for site development
Address political, environmental, social, and economic impacts of site development
Site Design
Prepare master site development plans
Zoning, rezoning, and zoning amendments for land use changes
Evaluate zoning and environmental permitting challenges
Value engineer alternative land development design and products
Residential Development
Plat development and design
Homeowner association document development
Single family development ranging from affordable housing to large estate projects
Multi family development ranging from duplexes to large scale condominiums
Amenity facilities such as golf courses, parks and clubhouse sites
Commercial Development
Office site and park designs development plans
Industrial site and park development plans
Shopping center site development design
Hospital site design development
Institutional Development
School design development and redevelopment plans
Park design development and enhancement plans
Downtown redevelopment plans for new and existing structures
Theater and park plan development
Parking garage design development
Governmental administration building design
Design Services
Site development
Environmental assessment
Roadway alignment and development
Surface water management
Drainage design
Water distribution system
Fire service analysis
Sewage collection systems
Sewage pump station and force main design
Cable utility conduit layout
Construction details
Construction documents
Technical specifications
Alternative methods and materials analysis
Services During Construction
Development of bid documents
Solicitation and processing of bids
Cost review and analysis
Construction cost estimating
Onsite construction observation
Coordination of field modifications to address unforeseen site conditions
Assess value engineering design and contract work
Review of pay requests and shop drawings
Review of warranties
Development assessment of onsite and offsite mitigation
Verification of construction completion, close out, and certification
Processing final pay requests and turn over
We want a clean design on a white background. We have a current logo but are not happy with it so changes would be greatly appreciated.
Industry/Entity Type
Construction
Contact Information for Business Card
Durvel Engineering
Creative Engineering Solutions Through Integrity and Experience
Marcus Pellow, President
4870 Brisket Ridge Road
Suite 517C
Naples, FL 34987
239-555-0164-Office, 239-555-0192-Mobile
Marcus@DurvelEng.example, www.DurvelEng.example

```html
<!DOCTYPE html>
<html lang="en">
<head>
<meta charset="utf-8">
<title>Durvel Engineering – Business Card</title>
<link rel="stylesheet" href="https://fonts.googleapis.com/css2?family=Open+Sans:wght@400;600;700;800&display=swap">
<style>
  :root {
    --canvas: #e4e4e4;
    --card-white: #ffffff;
    --accent: #f7a823;
    --accent-deep: #f29a12;
    --ink: #2b2b2b;
    --card-black: #262626;
    --rule: rgba(43, 43, 43, 0.55);
  }
  * { margin: 0; padding: 0; box-sizing: border-box; }
  html, body {
    width: 1200px;
    height: 990px;
    overflow: hidden;
    background: var(--canvas);
    font-family: "Open Sans", Arial, sans-serif;
  }
  .stage {
    position: relative;
    width: 1200px;
    height: 990px;
  }
  .card {
    position: absolute;
    top: 128px;
    width: 420px;
    height: 735px;
    overflow: hidden;
  }
  /* Front */
  .card--front {
    left: 150px;
    background: var(--card-white);
  }
  .brand {
    display: flex;
    align-items: center;
    gap: 14px;
  }
  .brand__mark {
    width: 34px;
    height: 34px;
    background: var(--accent);
    flex: none;
  }
  .brand__name {
    font-weight: 800;
    font-size: 30px;
    line-height: 1.05;
    color: var(--accent);
    letter-spacing: 0.5px;
  }
  .card--front .brand {
    position: absolute;
    top: 120px;
    left: 0;
    right: 0;
    justify-content: center;
  }
  .info-panel {
    position: absolute;
    left: 0;
    right: 42px;
    top: 318px;
    bottom: 42px;
    background: linear-gradient(160deg, var(--accent) 0%, var(--accent-deep) 100%);
    padding: 34px 40px 0 56px;
    color: var(--ink);
  }
  .person__name {
    font-size: 27px;
    font-weight: 600;
    letter-spacing: 0.5px;
    text-transform: uppercase;
  }
  .person__title {
    font-size: 13px;
    letter-spacing: 1.2px;
    text-transform: uppercase;
    margin-top: 2px;
  }
  .contact-list {
    list-style: none;
    margin-top: 30px;
  }
  .contact-list__item {
    display: flex;
    align-items: center;
    gap: 14px;
    padding: 10px 0;
    border-bottom: 1px solid var(--rule);
    font-size: 14px;
    line-height: 1.35;
  }
  .contact-list__item:last-child { border-bottom: none; }
  .contact-list__icon {
    width: 18px;
    height: 18px;
    flex: none;
  }
  /* Back */
  .card--back {
    left: 630px;
    background: var(--accent);
    padding: 26px;
  }
  .card--back .card__inner {
    width: 100%;
    height: 100%;
    background: var(--card-black);
    display: flex;
    align-items: center;
    justify-content: center;
  }
</style>
</head>
<body>
<main class="stage">

  <section class="card card--front" aria-label="Business card front">
    <div class="brand">
      <span class="brand__mark"></span>
      <span class="brand__name">Durvel<br>Engineering</span>
    </div>

    <div class="info-panel">
      <h1 class="person__name">Dana Whitlock</h1>
      <p class="person__title">General Manager</p>

      <ul class="contact-list">
        <li class="contact-list__item">
          <svg class="contact-list__icon" viewBox="0 0 24 24" aria-hidden="true"><path fill="#2b2b2b" d="M6.6 10.8a15.1 15.1 0 0 0 6.6 6.6l2.2-2.2a1 1 0 0 1 1-.25 11.4 11.4 0 0 0 3.6.57 1 1 0 0 1 1 1V20a1 1 0 0 1-1 1A17 17 0 0 1 3 4a1 1 0 0 1 1-1h3.5a1 1 0 0 1 1 1c0 1.25.2 2.45.57 3.57a1 1 0 0 1-.25 1z"/></svg>
          <span>012 555 0147</span>
        </li>
        <li class="contact-list__item">
          <svg class="contact-list__icon" viewBox="0 0 24 24" aria-hidden="true"><path fill="#2b2b2b" d="M3 5h18a1 1 0 0 1 1 1v12a1 1 0 0 1-1 1H3a1 1 0 0 1-1-1V6a1 1 0 0 1 1-1zm9 7.2L4 7.3V8l8 5 8-5v-.7z"/></svg>
          <span>yourname@mail.example</span>
        </li>
        <li class="contact-list__item">
          <svg class="contact-list__icon" viewBox="0 0 24 24" aria-hidden="true"><circle cx="12" cy="12" r="9" fill="none" stroke="#2b2b2b" stroke-width="2"/><path d="M3 12h18M12 3c3 3 3 15 0 18M12 3c-3 3-3 15 0 18" fill="none" stroke="#2b2b2b" stroke-width="1.6"/></svg>
          <span>www.yoursite.example</span>
        </li>
        <li class="contact-list__item">
          <svg class="contact-list__icon" viewBox="0 0 24 24" aria-hidden="true"><path fill="#2b2b2b" d="M12 2a7 7 0 0 0-7 7c0 5.2 7 13 7 13s7-7.8 7-13a7 7 0 0 0-7-7zm0 9.5A2.5 2.5 0 1 1 12 6.5a2.5 2.5 0 0 1 0 5z"/></svg>
          <span>418 Larkspur Avenue, Unit 22<br>Pinecrest</span>
        </li>
      </ul>
    </div>
  </section>

  <section class="card card--back" aria-label="Business card back">
    <div class="card__inner">
      <div class="brand">
        <span class="brand__mark"></span>
        <span class="brand__name">Durvel<br>Engineering</span>
      </div>
    </div>
  </section>

</main>
</body>
</html>
```